Velmora Freightway Solutions Business cards

Would like a very unique design catchy but professional for business cards. Please use log provided.Marlon WellsCeo and Founder TransCon Logistix Solutions1-888-913-3225mwells@tlsolutionsus.comwww.tlsolutionsus.com

```html
<!DOCTYPE html>
<html lang="en">
<head>
<meta charset="utf-8">
<title>Velmora Freightway Solutions – Business Cards</title>
<link rel="stylesheet" href="https://fonts.googleapis.com/css2?family=Cinzel:wght@700&family=Open+Sans:wght@400;600&display=swap">
<style>
  :root {
    --stage: #1c1c1e;
    --brand-blue: #0a72bb;
    --brand-red: #ec1f27;
    --paper: #ffffff;
    --ink-white: #ffffff;
  }
  * { margin: 0; padding: 0; box-sizing: border-box; }
  html, body { width: 1200px; height: 895px; overflow: hidden; }
  body { background: var(--stage); position: relative; font-family: "Open Sans", sans-serif; }

  .card {
    position: absolute;
    width: 540px;
    height: 309px;
    overflow: hidden;
    box-shadow: 0 14px 30px rgba(0,0,0,.55);
  }

  /* Front */
  .card--front { left: 90px; top: 100px; background: var(--brand-blue); }
  .card--front .brand {
    position: absolute; left: 0; right: 0; top: 112px;
    display: flex; align-items: center; justify-content: center; gap: 12px;
  }
  .brand-mark { width: 18px; height: 18px; background: currentColor; }
  .brand-name {
    font-family: "Cinzel", serif; font-weight: 700; font-size: 23px; letter-spacing: 1px;
  }
  .card--front .brand { color: var(--ink-white); }
  .card--front .brand-rule {
    position: absolute; left: 120px; right: 120px; top: 160px; height: 2px; background: var(--ink-white);
  }
  .card--front .site {
    position: absolute; left: 0; right: 0; top: 214px; text-align: center;
    color: var(--ink-white); font-size: 13px; letter-spacing: 1.5px;
  }

  /* Back */
  .card--back { left: 570px; top: 470px; background: var(--paper); }
  .card--back .brand {
    position: absolute; left: 0; right: 0; top: 62px;
    display: flex; align-items: center; justify-content: center; gap: 12px;
    color: var(--brand-blue);
  }
  .card--back .brand-rule {
    position: absolute; left: 130px; right: 130px; top: 104px; height: 2px; background: var(--brand-red);
  }
  .band {
    position: absolute; left: 0; right: 0; top: 142px; height: 112px;
    background: var(--brand-red); color: var(--ink-white);
    display: flex; align-items: center;
  }
  .person { width: 262px; text-align: right; padding-right: 22px; }
  .person-name { font-family: "Cinzel", serif; font-weight: 700; font-size: 19px; letter-spacing: .5px; }
  .person-role { font-size: 13px; line-height: 1.4; }
  .divider { width: 1px; height: 76px; background: rgba(255,255,255,.75); }
  .contacts { list-style: none; padding-left: 22px; font-size: 13px; line-height: 1.75; }
  .contacts li { display: flex; align-items: center; gap: 9px; }
  .contacts svg { width: 12px; height: 12px; fill: var(--ink-white); flex: none; }
</style>
</head>
<body>

<section class="card card--front" aria-label="Business card front">
  <div class="brand">
    <span class="brand-mark"></span>
    <span class="brand-name">Velmora Freightway Solutions</span>
  </div>
  <div class="brand-rule"></div>
  <p class="site">www.vfwayroutes.com</p>
</section>

<section class="card card--back" aria-label="Business card back">
  <div class="brand">
    <span class="brand-mark"></span>
    <span class="brand-name">Velmora Freightway Solutions</span>
  </div>
  <div class="brand-rule"></div>

  <div class="band">
    <div class="person">
      <p class="person-name">Dorian Pike</p>
      <p class="person-role">Ceo and Founder</p>
      <p class="person-role">Velmora Freightway Solutions</p>
    </div>
    <div class="divider"></div>
    <ul class="contacts">
      <li>
        <svg viewBox="0 0 24 24" aria-hidden="true"><path d="M6.6 10.8a15 15 0 0 0 6.6 6.6l2.2-2.2a1 1 0 0 1 1-.25 11.4 11.4 0 0 0 3.6.57 1 1 0 0 1 1 1V20a1 1 0 0 1-1 1A17 17 0 0 1 3 4a1 1 0 0 1 1-1h3.5a1 1 0 0 1 1 1c0 1.25.2 2.45.57 3.57a1 1 0 0 1-.25 1z"/></svg>
        1-888-470-6158
      </li>
      <li>
        <svg viewBox="0 0 24 24" aria-hidden="true"><path d="M2 5h20v14H2z M2 5l10 8 10-8" /></svg>
        dpike@vfwayroutes.com
      </li>
      <li>
        <svg viewBox="0 0 24 24" aria-hidden="true"><circle cx="12" cy="12" r="10"/></svg>
        www.vfwayroutes.com
      </li>
    </ul>
  </div>
</section>

</body>
</html>
```